Broschüre
Zielgruppe
Die T.O.R.K. Lumen Holding GmbH ist ein inhabergeführtes Immobilienunternehmen mit Sitz in Moers. Wir sind spezialisiert auf den direkten Ankauf von Mehrfamilienhäusern, Wohnanlagen und größeren Wohnimmobilien in Nordrhein-Westfalen. Unser Schwerpunkt liegt auf einer schnellen, diskreten und unbürokratischen Abwicklung – vom ersten Kontakt bis zum notariellen Abschluss. Wir kaufen Objekte in jedem Zustand, ob vermietet, leerstehend oder sanierungsbedürftig.
Wer ist Deine Zielgruppe?
• Institutionelle Eigentümer z.b. Wohnungsunternehmen und Investoren, die Bestände veräußern wollen
Aufgabenstellung
• Corporate Identity: Seriös, modern, vertrauenswürdig. Die Broschüre soll unsere Professionalität und Diskretion betonen.
• Farben: Anlehnung an die Unternehmensfarben der T.O.R.K. Lumen Holding GmbH (dezent, elegant, z. B. dunkles Blau, Grau, Weiß; ggf. Akzentfarbe Gold oder ein warmes Gelb).
• Schriftarten: Gut lesbar, modern, ohne verschnörkelte Fonts.
• Format: Hochformat DIN A4, 4–8 Seiten, übersichtlich und klar strukturiert.
• Bildsprache: Hochwertige Immobilienbilder, urbane Aufnahmen aus NRW, Detailfotos (z. B. Architektur, Gebäudeansichten) sowie emotionale Motive, die Vertrauen und Sicherheit vermitteln.
• Ton & Stil: Seriös, diskret, aber sympathisch – nicht zu werblich, sondern lösungsorientiert.
• Logo: Unser Firmenlogo muss auf dem Titel und der Rückseite gut sichtbar platziert sein.

```html
<!DOCTYPE html>
<html lang="de">
<head>
<meta charset="utf-8">
<title>T.O.R.K. Lumen Holding – Broschüre</title>
<link rel="stylesheet" href="https://fonts.googleapis.com/css2?family=Barlow:wght@300;400;500;600;700;800&display=swap">
<style>
:root{
  --navy:#1d2547;
  --navy-card:#263058;
  --gold:#c9a13a;
  --paper:#ffffff;
  --paper-soft:#f3f3f5;
  --ink:#2b2f3a;
  --muted:#6d7180;
  --stage:#dcdcde;
}
*{box-sizing:border-box;margin:0;padding:0}
html,body{width:1200px;height:4929px;overflow:hidden}
body{background:var(--stage);font-family:'Barlow',sans-serif;color:var(--ink);padding:44px 170px}
.page{position:relative;width:860px;height:1180px;margin-bottom:40px;overflow:hidden;background:var(--paper);box-shadow:0 6px 20px rgba(0,0,0,.18)}
.page:last-child{margin-bottom:0}
.band{position:absolute;left:0;right:0;bottom:0;background:var(--navy);border-top:6px solid var(--gold);color:#fff}
.brand{font-weight:700;color:var(--navy);letter-spacing:.04em;display:flex;align-items:center;gap:14px}
.brand .mark{background:var(--gold);display:inline-block}

/* back cover */
.back .top{position:absolute;inset:0 0 310px 0;background:var(--paper-soft);text-align:center}
.back .brand{justify-content:center;flex-direction:column;font-size:44px;margin-top:190px;gap:22px}
.back .brand .mark{width:60px;height:60px}
.back .brand small{font-size:22px;letter-spacing:.18em;font-weight:700}
.back h2{font-weight:500;font-size:30px;line-height:1.35;margin-top:170px;color:var(--ink)}
.back .claim{font-size:19px;color:var(--muted);margin-top:18px}
.back .band{height:310px;display:flex;align-items:center;padding:0 80px;gap:90px}
.contact-title{font-weight:800;font-size:52px;line-height:.95;color:var(--gold)}
.contact-list{list-style:none;font-size:17px;color:#d8dae3}
.contact-list li{display:flex;align-items:center;gap:14px;margin:12px 0}
.contact-list svg{flex:none}

/* front cover */
.front .photo{position:absolute;inset:0 0 310px 0;background:linear-gradient(180deg,#8fb8e6 0%,#c7dcf0 30%,#9c6a4e 52%,#8a5b41 68%,#6f8f3f 86%,#5d7d37 100%)}
.front .brand{position:absolute;top:34px;right:40px;font-size:22px;color:var(--navy);gap:10px}
.front .brand .mark{width:22px;height:22px}
.front .band{height:310px;padding:60px 60px}
.front .kicker{font-weight:300;font-size:54px;color:var(--gold);letter-spacing:.02em;line-height:1}
.front h1{font-weight:800;font-size:62px;letter-spacing:.01em;line-height:1.1;margin-top:8px}
.front h1 em{font-style:normal;color:var(--gold)}
.front .sub{font-size:16px;color:#c9ccd8;margin-top:18px}

/* inner pages */
.inner .band{height:520px;padding:44px 46px}
.eyebrow{font-weight:500;font-size:30px;line-height:1.15;color:var(--navy)}
.eyebrow span{display:block;color:var(--gold)}
.band .eyebrow{color:#fff}
.body-copy{font-size:14px;line-height:1.55;color:var(--muted);margin-top:14px}
.invest .photo{position:absolute;left:30px;top:40px;width:330px;height:560px;background:linear-gradient(160deg,#e9ecef 0%,#c9ced4 45%,#3a3a40 100%);clip-path:polygon(0 0,45% 15%,100% 0,100% 100%,45% 85%,0 100%)}
.invest .copy{position:absolute;left:400px;right:40px;top:50px}
.steps{display:grid;grid-template-columns:1fr 1fr;gap:18px;margin-top:26px}
.step{background:var(--navy-card);padding:20px 18px;min-height:150px}
.step h4{display:flex;align-items:center;gap:12px;font-weight:600;font-size:16px}
.step p{font-size:13px;color:#b9bdcc;line-height:1.5;margin-top:14px}
.dot{width:34px;height:34px;border-radius:50%;background:var(--gold);display:flex;align-items:center;justify-content:center;color:var(--navy);font-weight:700;font-size:16px;flex:none}
.intro{font-size:14px;color:#b9bdcc;margin-top:14px}

.profile .copy{position:absolute;left:46px;top:50px;width:440px}
.profile .photo{position:absolute;right:40px;top:40px;width:300px;height:560px;background:linear-gradient(180deg,#6f9bd6 0%,#a9c6ea 35%,#9b5a40 55%,#7d4632 70%,#6e9a3d 85%,#557b2f 100%)}
.ticks{list-style:none;margin-top:18px;font-size:14px;color:var(--muted);line-height:1.45}
.ticks li{position:relative;padding-left:22px;margin:12px 0}
.ticks li::before{content:"";position:absolute;left:0;top:5px;width:9px;height:9px;border-radius:50%;background:var(--gold)}
.note{font-size:14px;color:var(--muted);margin-top:22px;line-height:1.5}
.note strong{color:var(--ink);display:block}
.quote-mark{position:absolute;right:50px;top:24px;font-weight:800;font-size:150px;color:var(--gold);line-height:1}
.reviews{display:grid;grid-template-columns:repeat(3,1fr);gap:16px;margin-top:50px}
.review{background:var(--navy-card);padding:20px 16px;min-height:290px}
.review header{display:flex;align-items:center;gap:10px}
.review b{font-weight:600;font-size:15px;display:block}
.review small{font-size:11px;color:#9da2b6}
.review p{font-size:13px;color:#b9bdcc;line-height:1.55;margin-top:18px}
.fold{position:absolute;top:-6px;width:0;height:0;border-left:22px solid transparent;border-right:22px solid transparent;border-top:26px solid var(--gold)}
</style>
</head>
<body>

<section class="page back" aria-label="Rückseite">
  <div class="top">
    <div class="brand"><span class="mark"></span>T.O.R.K. LUMEN<small>HOLDING</small></div>
    <h2>Verkaufen Sie Ihr Mehrfamilienhaus<br>an einen verlässlichen Partner</h2>
    <p class="claim">Unsere Erfahrung, unsere Zuverlässigkeit, Ihr Vorteil.</p>
  </div>
  <div class="band">
    <div class="contact-title">Contact<br>Us</div>
    <ul class="contact-list">
      <li><svg width="16" height="16" viewBox="0 0 16 16"><rect width="16" height="16" fill="#c9a13a"/><path d="M8 3a3 3 0 0 0-3 3c0 2.5 3 6 3 6s3-3.5 3-6a3 3 0 0 0-3-3z" fill="#1d2547"/></svg>Lindenallee 48, 47441 Moers</li>
      <li><svg width="16" height="16" viewBox="0 0 16 16"><rect width="16" height="16" fill="#c9a13a"/><path d="M5 3l2 2-1 1.5c.7 1.4 1.8 2.5 3.5 3.5L11 9l2 2-1.5 2C7 12.5 3.5 9 3 4.5z" fill="#1d2547"/></svg>0284 193 5520</li>
      <li><svg width="16" height="16" viewBox="0 0 16 16"><rect width="16" height="16" fill="#c9a13a"/><path d="M3 5h10v7H3z M3 5l5 4 5-4" fill="none" stroke="#1d2547" stroke-width="1.4"/></svg>kontakt@tork-lumen.de</li>
    </ul>
  </div>
</section>

<section class="page front" aria-label="Titelseite">
  <div class="photo" role="img" aria-label="Foto: Mehrfamilienhaus aus Backstein mit Balkonen und Rasenfläche unter blauem Himmel"></div>
  <div class="brand"><span class="mark"></span>T.O.R.K. LUMEN</div>
  <div class="band">
    <p class="kicker">WIR KAUFEN</p>
    <h1>IMMOBILIEN IN <em>NRW</em></h1>
    <p class="sub">Wohnungsunternehmen | Privatverkäufer &amp; Erbengemeinschaften | Tippgeber werden</p>
  </div>
</section>

<section class="page inner invest" aria-label="Innenseite links">
  <div class="photo" role="img" aria-label="Foto: lächelnde Ansprechpartnerin im Büro"></div>
  <div class="copy">
    <h2 class="eyebrow">WIR INVESTIEREN<span>IN WERTE, DIE BLEIBEN.</span></h2>
    <p class="body-copy">Als inhabergeführtes Immobilienunternehmen mit Sitz in der Region stehen wir für Verlässlichkeit, Diskretion und nachhaltige Qualität. Wir kaufen Wohnimmobilien – insbesondere Mehrfamilienhäuser – von privaten Eigentümern, Erbengemeinschaften und institutionellen Verkäufern. Dabei zählen keine Versprechungen, sondern klare Entscheidungen.</p>
    <p class="body-copy">Wir wissen, dass jedes Objekt einzigartig ist. Deshalb setzen wir auf individuelle Lösungen, die genau zu Ihrer Situation passen. Als Verkäufer profitieren Sie von einer schnellen Abwicklung und sicherer Liquidität.</p>
    <p class="body-copy">Unser Hauptaugenmerk liegt auf Mehrfamilienhäusern in den Städten Moers, Neukirchen-Vluyn, Kamp-Lintfort und Duisburg.</p>
  </div>
  <div class="band">
    <span class="fold" style="right:0"></span>
    <h3 class="eyebrow">IMMOBILIE VERKAUFEN – EINFACH,<span>SCHNELL, SICHER</span></h3>
    <p class="intro">Mit T.O.R.K. Lumen Holding ist der Immobilienverkauf unkompliziert und transparent.</p>
    <div class="steps">
      <article class="step"><h4><span class="dot">1</span>Anfrage senden</h4><p>Sie senden uns die Eckdaten Ihrer Immobilie – online oder telefonisch.</p></article>
      <article class="step"><h4><span class="dot">2</span>Rückmeldung in 24h</h4><p>Wir melden uns schnellstmöglich bei Ihnen mit einer ersten Einschätzung.</p></article>
      <article class="step"><h4><span class="dot">3</span>Besichtigung &amp; Angebot</h4><p>Nach der Besichtigung erhalten Sie ein verbindliches Kaufangebot.</p></article>
      <article class="step"><h4><span class="dot">4</span>Notartermin &amp; Verkauf</h4><p>Wir übernehmen alle Formalitäten – schnell, rechtssicher und ohne Provision.</p></article>
    </div>
  </div>
</section>

<section class="page inner profile" aria-label="Innenseite rechts">
  <div class="copy">
    <h2 class="eyebrow">UNSER<span>ANKAUFSPROFIL</span></h2>
    <p class="body-copy">Wir suchen gezielt Wohnimmobilien in NRW mit Fokus auf:</p>
    <ul class="ticks">
      <li>Mehrfamilienhäuser</li>
      <li>Lage: Moers, Duisburg, Kamp-Lintfort, Neukirchen-Vluyn und Umgebung</li>
      <li>Auch sanierungsbedürftige Objekte</li>
      <li>Wir kaufen direkt – von kleineren Mehrfamilienhäusern bis hin zu Wohnportfolios mit einem Volumen bis 15 Mio. €</li>
    </ul>
    <p class="note">Sie bieten eine Immobilie oder ein Portfolio an? Wir prüfen jedes Angebot schnell, diskret und fair.<strong>Egal ob vermietet, leerstehend oder sanierungsbedürftig.</strong></p>
  </div>
  <div class="photo" role="img" aria-label="Foto: Backstein-Mehrfamilienhaus mit Baum im Vordergrund"></div>
  <div class="band">
    <span class="fold" style="left:0"></span>
    <h3 class="eyebrow">WAS SIE<span>ÜBER UNS SAGEN</span></h3>
    <div class="quote-mark" aria-hidden="true">“</div>
    <div class="reviews">
      <article class="review"><header><span class="dot">K</span><div><b>K. Albers</b><small>Verkäufer, Moers</small></div></header><p>„Innerhalb von zwei Wochen war der Kaufvertrag unterschrieben – das hätte ich nie für möglich gehalten. Der gesamte Prozess war professionell, schnell und von Anfang an transparent.“</p></article>
      <article class="review"><header><span class="dot">R</span><div><b>R. Hoffmann</b><small>Erbengemeinschaft, Duisburg</small></div></header><p>„Ich hatte zuerst Bedenken, meine Immobilie zu verkaufen, aber das Gespräch war ehrlich und kompetent. Die Verkaufspreise entsprach genau meinen Erwartungen. Vielen Dank!“</p></article>
      <article class="review"><header><span class="dot">S</span><div><b>S. Lindner</b><small>Verkäuferin, Kamp-Lintfort</small></div></header><p>„Ich habe keine Erfahrung mit Immobilienverkäufen, aber das Team hat mich Schritt für Schritt begleitet. Alle Fragen wurden ausführlich beantwortet.“</p></article>
    </div>
  </div>
</section>

</body>
</html>
```